Marwick Law Letterhead

We need a new letterhead design for a Law Firm. The address for the law firm is 1475 Calloway Street, Suite 210, Houston, Texas 77041. Phone Number: 832-361-9027; Fax Number: 832-614-7359. The logo is uploaded to the project.

```html
<!DOCTYPE html>
<html lang="en">
<head>
<meta charset="utf-8">
<title>Marwick Law Letterhead</title>
<link rel="stylesheet" href="https://fonts.googleapis.com/css2?family=Open+Sans:wght@400;600&family=Lato:wght@400&display=swap">
<style>
  :root {
    --navy: #172c55;
    --red: #c8202a;
    --red-dark: #9c1820;
    --ink: #3d3d3d;
    --ink-strong: #2a2a2a;
    --paper: #ffffff;
    --backdrop: #e6e6e6;
  }
  * { margin: 0; padding: 0; box-sizing: border-box; }
  html, body { width: 1040px; height: 1200px; overflow: hidden; background: var(--backdrop); }
  .letterhead {
    position: absolute; left: 60px; top: 8px;
    width: 920px; height: 1185px;
    background: var(--paper);
    box-shadow: 0 2px 10px rgba(0,0,0,.18);
    font-family: "Open Sans", sans-serif; color: var(--ink);
    overflow: hidden;
  }
  .side-band { position: absolute; left: 0; top: 0; width: 16px; height: 100%; background: var(--navy); }
  .brand {
    position: absolute; top: 50px; left: 0; width: 100%;
    display: flex; justify-content: center; align-items: center; gap: 14px;
  }
  .brand-mark { width: 30px; height: 30px; background: var(--navy); }
  .brand-name { font-size: 40px; font-weight: 600; color: var(--navy); letter-spacing: .5px; }
  .letter-body { position: absolute; left: 86px; width: 744px; font-size: 14.5px; }
  .issue-date { top: 214px; }
  .recipient { top: 250px; line-height: 18px; }
  .salutation { top: 352px; }
  .paragraph { line-height: 26.5px; text-align: justify; }
  .p1 { top: 406px; } .p2 { top: 566px; } .p3 { top: 672px; }
  .closing { top: 804px; }
  .signature {
    position: absolute; left: 86px; top: 838px; width: 214px; height: 28px;
    background: linear-gradient(90deg, #d9d9d9, #f2f2f2);
  }
  .signatory { top: 879px; font-size: 18px; font-weight: 600; color: var(--ink-strong); }
  .signatory-title { top: 912px; }
  .contact-art { position: absolute; left: 0; top: 0; }
  .contact-line {
    position: absolute; left: 50px; font-family: "Lato", sans-serif;
    font-size: 17px; color: #111;
  }
  .phone { top: 1034px; } .fax { top: 1071px; } .address { top: 1110px; }
</style>
</head>
<body>
<main class="letterhead">
  <div class="side-band"></div>

  <header class="brand">
    <span class="brand-mark"></span>
    <span class="brand-name">Marwick Law</span>
  </header>

  <p class="letter-body issue-date">Issuing Date: May 5, 2018</p>
  <p class="letter-body recipient">Name Of Employee Mr. XYZABC<br>Address of Employee<br>Address Line 2 etc..</p>
  <p class="letter-body salutation">Dear Mr.XYZABC</p>

  <p class="letter-body paragraph p1">Lorem Ipsum has been the industry's standard dummy text ever since the 1500s, when an unknown printer took a galley of type and scrambled it to make a type specimen book. It has survived not only five centuries, but also the leap into electronic typesetting, remaining essentially unchanged. It was popularised in the 1960s with the release of Letraset sheets containing Lorem Ipsum passages, and more recently with desktop publishing software like Aldus PageMaker including versions of Lorem Ipsum.</p>
  <p class="letter-body paragraph p2">Lorem Ipsum is simply dummy text of the printing and typesetting industry. Lorem Ipsum has been the industry's standard dummy text ever since the 1500s, when an unknown printer took a galley of type and scrambled it to make a type specimen book.</p>
  <p class="letter-body paragraph p3">It has survived not only five centuries, but also the leap into electronic typesetting, remaining essentially unchanged. It was popularised in the 1960s with the release of Letraset sheets containing Lorem IpsumIpsum passages.</p>

  <p class="letter-body closing">Yours Sincerely</p>
  <div class="signature" role="img" aria-label="Handwritten signature of Everett Crane"></div>
  <p class="letter-body signatory">Everett Crane</p>
  <p class="letter-body signatory-title">Managing Director</p>

  <svg class="contact-art" width="60" height="1185" viewBox="0 0 60 1185" aria-hidden="true">
    <polygon points="0,985 16,985 42,1004 42,1185 0,1185" fill="var(--navy)"/>
    <polygon points="0,1030 40,1014 40,1046 0,1062" fill="var(--red)"/>
    <polygon points="0,1068 40,1052 40,1084 0,1100" fill="var(--red)"/>
    <polygon points="0,1106 40,1090 40,1124 0,1140" fill="var(--red)"/>
    <!-- phone -->
    <path d="M18 1029 q-2 -2 0 -4 l2 -2 l3 4 l-1.5 1.5 q1 3 4 4.5 l1.5 -1.5 l4 3 l-2 2 q-2 2 -5 0 q-5 -3 -6 -7.5z" fill="#fff"/>
    <!-- printer -->
    <rect x="20" y="1060" width="10" height="4" fill="#fff"/>
    <rect x="16" y="1065" width="18" height="8" rx="1.5" fill="#fff"/>
    <rect x="20" y="1071" width="10" height="6" fill="#fff" stroke="var(--red)" stroke-width="1"/>
    <!-- pin -->
    <path d="M24 1120 c-4 -5 -6 -8 -6 -11 a6 6 0 0 1 12 0 c0 3 -2 6 -6 11z" fill="#fff"/>
    <circle cx="24" cy="1109" r="2.2" fill="var(--red)"/>
  </svg>

  <p class="contact-line phone">832-361-9027</p>
  <p class="contact-line fax">832-614-7359</p>
  <p class="contact-line address">1475 Calloway Street, Suite 210, Houston, Texas 77041</p>
</main>
</body>
</html>
```